Business Card Design for Marketing Firm

Looking for business card design for higher end marketing firm. Clean but impressionable/trendy. We are a marketing firm that represents manufacturers in the foodservice equipment and supply industry. Our customers are end users such has hotels, restaurants, country clubs, convention centers and casinos as well as distributors of restaurants supplies and equipment, and manufacturers of foodservice equipment and supplies.
Target Market(s)
Hotels, Restaurants, Supply & Equipment Distributors, Foodservice Manufacturers
Industry/Entity Type
Foodservice/Hospitality
Contact Information for Business Card
Name, Title, Contact Number, Email, Website, Social Media, Address
Requirements
Must have
- Clean & Simple but Serious and Impressionable

```html
<!DOCTYPE html>
<html lang="en">
<head>
<meta charset="utf-8">
<title>Harbor Hospitality Reps – Business Cards</title>
<link href="https://fonts.googleapis.com/css2?family=Cinzel:wght@500&family=Open+Sans:wght@400;700&display=swap" rel="stylesheet">
<style>
  :root{
    --navy:#262673;
    --ink:#2b2b3a;
    --paper:#ffffff;
    --backdrop:#3a3431;
  }
  *{margin:0;padding:0;box-sizing:border-box}
  html,body{width:1200px;height:786px;overflow:hidden;background:var(--backdrop)}
  .stage{position:relative;width:1200px;height:786px}
  .card{position:absolute;top:238px;width:540px;height:309px;background:var(--paper);overflow:hidden;box-shadow:0 10px 30px rgba(0,0,0,.35)}
  .card--contact{left:40px}
  .card--brand{left:620px;border-bottom:6px solid var(--navy)}
  .card__wave{position:absolute;left:0;top:0;width:540px;height:309px}
  .brand{position:absolute;text-align:center;color:var(--navy);font-family:"Cinzel",serif;font-weight:500;letter-spacing:.04em}
  .brand__mark{display:block;margin:0 auto 12px;border-radius:50%;border:2px solid var(--navy)}
  .brand__name{display:block;line-height:1.05}
  .brand__rule{display:block;height:1.5px;background:var(--navy);margin:6px auto 0}
  .card--contact .brand{left:24px;top:48px;width:250px}
  .card--contact .brand__mark{width:46px;height:46px}
  .card--contact .brand__name{font-size:21px}
  .card--contact .brand__rule{width:200px}
  .divider{position:absolute;left:290px;top:40px;width:1.5px;height:136px;background:var(--navy)}
  .contact{position:absolute;left:308px;top:32px;font-family:"Open Sans",sans-serif;color:var(--ink)}
  .contact__name{font-weight:700;font-size:17px;line-height:23px;color:var(--navy);letter-spacing:.01em}
  .contact__title{font-size:11px;line-height:16px;margin-bottom:8px}
  .contact__list{list-style:none;font-size:11.5px;line-height:17px}
  .contact__list li{display:flex;align-items:center;gap:6px}
  .contact__list svg{width:10px;height:10px;flex:none}
  .contact__address{font-size:11.5px;line-height:16px;margin-top:8px}
  .card--brand .brand{left:0;top:70px;width:540px}
  .card--brand .brand__mark{width:60px;height:60px}
  .card--brand .brand__name{font-size:30px}
  .card--brand .brand__rule{width:330px}
  .social{display:flex;justify-content:center;gap:4px;margin-top:10px}
  .social span{width:13px;height:13px;border-radius:50%;background:var(--navy)}
</style>
</head>
<body>
<main class="stage">
  <section class="card card--contact" aria-label="Business card, contact side">
    <svg class="card__wave" viewBox="0 0 540 309" aria-hidden="true">
      <path d="M0 272 C120 272 220 252 310 215 C390 182 460 172 540 170 L540 309 L0 309 Z" fill="var(--navy)"/>
      <path d="M90 278 C200 274 250 252 330 218 C400 188 460 178 510 176 C450 184 400 198 340 228 C260 264 190 280 90 278 Z" fill="var(--paper)"/>
    </svg>
    <div class="brand">
      <span class="brand__mark"></span>
      <span class="brand__name">Harbor Hospitality<br>Reps</span>
      <span class="brand__rule"></span>
    </div>
    <div class="divider"></div>
    <div class="contact">
      <p class="contact__name">DANIEL HART</p>
      <p class="contact__title">Managing Director</p>
      <ul class="contact__list">
        <li><svg viewBox="0 0 10 10"><path d="M2 1 L4 3 L3 4 C4 6 5 7 6 7 L7 6 L9 8 L8 9 C4 9 1 6 1 2 Z" fill="var(--navy)"/></svg>123 456 789</li>
        <li><svg viewBox="0 0 10 10"><rect x="0.5" y="2" width="9" height="6.5" fill="none" stroke="var(--navy)"/><path d="M0.5 2 L5 6 L9.5 2" fill="none" stroke="var(--navy)"/></svg>info@yourgmail.com</li>
        <li><svg viewBox="0 0 10 10"><circle cx="5" cy="5" r="4.5" fill="var(--navy)"/><path d="M0.5 5 H9.5 M5 0.5 V9.5" stroke="#fff" stroke-width=".7"/></svg>www.yourwebsite.com</li>
      </ul>
      <p class="contact__address">Your address, City<br>State, Zip 1234</p>
    </div>
  </section>

  <section class="card card--brand" aria-label="Business card, brand side">
    <div class="brand">
      <span class="brand__mark"></span>
      <span class="brand__name">Harbor Hospitality Reps</span>
      <span class="brand__rule"></span>
      <div class="social" aria-label="Social media links">
        <span></span><span></span><span></span><span></span><span></span><span></span>
      </div>
    </div>
  </section>
</main>
</body>
</html>
```